Ward Compass Business Card Design*

We need a business card design for our company Ward Compass. Our company is specialized in providing online consulting services regarding medical institutions, hospitals and doctors. We work with patients worldwide looking to choose between healthcare providers. We have a website you may use as a reference, where we list doctors and clinics worldwide. So we target Medical providers as well as patients worldwide.
Target Market(s)
Medical Providers and patients around the world
Industry/Entity Type
Medical
Contact Information for Business Card
Salwa Kettani
CEO
+90 612 348 2175
info@wardcompass.example
www.wardcompass.example
14 Annakhil 7 H.R.B. Rabat, Morocco
Requirements
Must have
- Company logo/name on one full side, personal info and smaller logo and company name on the other side.
Nice to have
- Smart and elegant design

```html
<!DOCTYPE html>
<html lang="en">
<head>
<meta charset="utf-8">
<title>Ward Compass — Business Card</title>
<link rel="stylesheet" href="https://fonts.googleapis.com/css2?family=Montserrat:wght@600&family=Open+Sans:wght@400;600&display=swap">
<style>
  :root {
    --navy: #143866;
    --grey: #85878a;
    --white: #ffffff;
    --backdrop: #e6e8eb;
  }
  * { margin: 0; padding: 0; box-sizing: border-box; }
  html, body {
    width: 1200px; height: 1000px; overflow: hidden;
    background: var(--backdrop);
  }
  .sheet {
    position: relative; width: 1200px; height: 1000px;
  }
  .card {
    position: absolute; left: 250px; width: 700px; height: 400px;
    overflow: hidden;
    box-shadow: 0 6px 18px rgba(0,0,0,0.18);
  }
  .card-front { top: 60px; background: var(--navy); }
  .card-back { top: 520px; background: var(--navy); }

  /* Front side */
  .front-brand {
    position: absolute; inset: 0;
    display: flex; align-items: center; justify-content: center; gap: 22px;
  }
  .brand-dot {
    width: 70px; height: 70px; border-radius: 50%; background: var(--white);
  }
  .brand-name {
    font-family: "Montserrat", sans-serif; font-weight: 600;
    letter-spacing: 1px; text-transform: uppercase; white-space: nowrap;
  }
  .front-brand .brand-name { color: var(--white); font-size: 42px; }

  /* Back side */
  .back-upper {
    position: absolute; left: 0; top: 0; width: 100%; height: 200px;
    background: var(--white);
  }
  .back-upper .brand-name {
    position: absolute; left: 0; right: 0; top: 62px; text-align: center;
    color: var(--navy); font-size: 40px;
  }
  .back-disc {
    position: absolute; left: 278px; top: 128px;
    width: 130px; height: 130px; border-radius: 50%;
    background: var(--white);
  }
  .holder {
    position: absolute; right: 372px; top: 278px; text-align: right;
    font-family: "Open Sans", sans-serif; color: var(--white);
  }
  .holder-name { font-weight: 600; font-size: 21px; letter-spacing: 0.5px; text-transform: uppercase; }
  .holder-role { font-weight: 600; font-size: 18px; margin-top: 4px; }
  .divider {
    position: absolute; left: 345px; top: 278px; width: 1px; height: 70px;
    background: var(--white);
  }
  .contacts {
    position: absolute; left: 362px; top: 272px; list-style: none;
    font-family: "Open Sans", sans-serif; color: var(--white); font-size: 16px;
  }
  .contacts li { display: flex; align-items: center; gap: 10px; height: 27px; }
  .contacts svg { width: 15px; height: 15px; flex: none; }
  .address {
    position: absolute; left: 150px; top: 358px;
    font-family: "Open Sans", sans-serif; color: var(--white); font-size: 16px;
  }
</style>
</head>
<body>
<main class="sheet">
  <section class="card card-front" aria-label="Card front">
    <div class="front-brand">
      <span class="brand-dot"></span>
      <span class="brand-name">Ward Compass</span>
    </div>
  </section>

  <section class="card card-back" aria-label="Card back">
    <div class="back-upper">
      <span class="brand-name">Ward Compass</span>
    </div>
    <span class="back-disc"></span>

    <div class="holder">
      <p class="holder-name">Salwa Kettani</p>
      <p class="holder-role">CEO</p>
    </div>
    <span class="divider"></span>

    <ul class="contacts">
      <li>
        <svg viewBox="0 0 24 24" fill="var(--white)"><path d="M6.6 10.8a15.1 15.1 0 0 0 6.6 6.6l2.2-2.2a1 1 0 0 1 1-.25 11.4 11.4 0 0 0 3.6.57 1 1 0 0 1 1 1V20a1 1 0 0 1-1 1A17 17 0 0 1 3 4a1 1 0 0 1 1-1h3.5a1 1 0 0 1 1 1c0 1.25.2 2.45.57 3.57a1 1 0 0 1-.25 1z"/></svg>
        <span>+90 612 348 2175</span>
      </li>
      <li>
        <svg viewBox="0 0 24 24" fill="none" stroke="var(--white)" stroke-width="2"><rect x="3" y="5" width="18" height="14"/><path d="M3 6l9 7 9-7"/></svg>
        <span>info@wardcompass.example</span>
      </li>
      <li>
        <svg viewBox="0 0 24 24" fill="none" stroke="var(--white)" stroke-width="2"><circle cx="12" cy="12" r="9"/><path d="M3 12h18M12 3c3 3 3 15 0 18M12 3c-3 3-3 15 0 18"/></svg>
        <span>www.wardcompass.example</span>
      </li>
    </ul>

    <p class="address">14 Annakhil 7 H.R.B. Rabat, Morocco</p>
  </section>
</main>
</body>
</html>
```